Brightwave Reach - Business Card

We need a business card for a Social Media Marketing company that specializes in online marketing for small businesses in Canada using common Social Media platforms such as Pixlora, Chatterly, Blinkpost & Quibber.

I have uploaded a copy of our logo which I would like utilized in the business card. We would like the business card to be modern yet classy design.

Our website is www.brightwavereach.ca

Industry/Entity Type

Marketing

Contact Information for Business Card

Email: info@brightwavereach.ca
Website: www.brightwavereach.ca
Telephone: 604-555-0193

Colors

Designer to choose colors to be used in the design.

Requirements
Must have
• Social Media icons on reverse
• Please add some designs with color.

```html
<!DOCTYPE html>
<html lang="en">
<head>
<meta charset="utf-8">
<title>Brightwave Reach – Business Card</title>
<link href="https://fonts.googleapis.com/css2?family=Roboto+Condensed:wght@400;700&family=Roboto:wght@400;500&display=swap" rel="stylesheet">
<style>
  :root{
    --backdrop:#2a2b2d;
    --card-front:#f7f7f5;
    --ink:#3a3a3a;
    --card-back-dark:#35383b;
    --card-back-light:#6a7074;
    --light-text:#ffffff;
    --soft-text:#e4e6e7;
  }
  *{margin:0;padding:0;box-sizing:border-box}
  html,body{width:1200px;height:900px;overflow:hidden;background:var(--backdrop)}
  .canvas{position:relative;width:1200px;height:900px}
  .card{position:absolute;left:280px;width:640px;height:366px}
  .card-front{top:69px;background:var(--card-front);display:flex;flex-direction:column;align-items:center;justify-content:center}
  .brand{display:flex;align-items:center;gap:14px;margin-top:-10px}
  .brand-square{width:22px;height:22px;background:var(--ink)}
  .brand-name{font-family:"Roboto Condensed",sans-serif;font-weight:700;font-size:46px;letter-spacing:1px;color:var(--ink);text-transform:uppercase}
  .social-list{display:flex;gap:18px;margin-top:52px;list-style:none}
  .social-item{display:flex;align-items:center;gap:6px;font-family:"Roboto",sans-serif;font-size:13px;color:var(--ink)}
  .social-dot{width:20px;height:20px;border:1.5px solid var(--ink);border-radius:50%}
  .card-back{top:465px;background:linear-gradient(120deg,var(--card-back-dark) 0%,var(--card-back-light) 100%);display:flex;align-items:center;justify-content:center}
  .identity{text-align:right;padding-right:30px}
  .person-name{font-family:"Roboto Condensed",sans-serif;font-weight:700;font-size:36px;color:var(--light-text);line-height:1}
  .person-role{font-family:"Roboto",sans-serif;font-size:17px;color:var(--soft-text);margin-top:8px}
  .divider{width:2px;height:104px;background:var(--light-text)}
  .contact-list{list-style:none;padding-left:28px}
  .contact-item{display:flex;align-items:center;gap:10px;font-family:"Roboto",sans-serif;font-weight:500;font-size:16px;color:var(--light-text);line-height:26px}
  .contact-icon{width:14px;height:14px;fill:var(--light-text)}
</style>
</head>
<body>
<main class="canvas">
  <section class="card card-front">
    <div class="brand">
      <span class="brand-square"></span>
      <span class="brand-name">Brightwave Reach</span>
    </div>
    <ul class="social-list">
      <li class="social-item"><span class="social-dot"></span>Chatterly</li>
      <li class="social-item"><span class="social-dot"></span>Pixlora</li>
      <li class="social-item"><span class="social-dot"></span>Quibber</li>
    </ul>
  </section>

  <section class="card card-back">
    <div class="identity">
      <h1 class="person-name">MARCUS HALE</h1>
      <p class="person-role">CEO/FOUNDER</p>
    </div>
    <span class="divider"></span>
    <ul class="contact-list">
      <li class="contact-item">
        <svg class="contact-icon" viewBox="0 0 16 16"><path d="M3.5 1l2.5 3-1.5 1.8c.9 2 2.6 3.7 4.7 4.7L11 9l3 2.5-1.3 2.8C7 14 2 9 1.7 3.3z"/></svg>
        604-555-0193
      </li>
      <li class="contact-item">
        <svg class="contact-icon" viewBox="0 0 16 16"><path d="M1 3h14v10H1zM2 4.2V12h12V4.2L8 8.8z"/><path d="M2 3.5l6 4.5 6-4.5z"/></svg>
        info@brightwavereach.ca
      </li>
      <li class="contact-item">
        <svg class="contact-icon" viewBox="0 0 16 16"><circle cx="8" cy="8" r="7"/></svg>
        www.brightwavereach.ca
      </li>
    </ul>
  </section>
</main>
</body>
</html>
```